Tradlo - Forex Signal Services Moments Matter Most. Reshape your path.

I need an attractive eye catching web design that is azure friendly. I currently have a web programmer working on the backend of my website. Now I need a professional design to attract and retain customers. This site needs to be mobile friendly.

Tradlo is a highly reputable, trustworthy and professional site that offers forex signals to traders in all parts of the globe. With accurate and reliable forex signals, traders can not only make money but also boost their profits.

At Tradlo, we want our clients to have complete faith on us and our services! We also do not want our users to lead a simple and monotonous life. Instead our goal is to help them create an extra source of steady income. However, this is possible only when our clients resolve to change their lives for the better. They need to change their mindset and most importantly develop a positive frame of mind. That’s exactly why at Tradlo, we provide our clients with innumerable personal development tools and resources that’ll aid them in changing all the aspects of their lives. We want our traders to feel inspired and educate them in the right way!

Colors are flexible.

I do like the simplicity of www.brightmarkvo.example.
I do want a design more professional in appearance and not everything on page one.

I have not been able to decide on a logo. There is one of lower quality as I have not paid for it yet but I will if you decide it's the best for my business I will. Or should one feel that they have a better idea for a logo, I will pay for it if i like it.

I have included some of the content of my site so you can get a feel for where I am coming from.
(Please note that this content is still in the editing process)
Updates

Project Deadline Extended Reason: My content was not complete nor finalization of the final logo. We will allow a few more days for designers to modify the website.Thank you for your patience and understanding. Added Tuesday, January 24, 2017

Target Market(s)

I work with Forex Traders, Investors wanting to control their own portfolios, and remote nomads/mellienials

Coding

Coded - Design and coding required

Number of Pages Required

5+ page

Requirements
Must have
• I must have a professional clean look. I want the site to be interactive and eye catching. I want my audience hooked within seconds of opening it. It has to have all important information first. Photos must be legit and not spammy. I work as a representative in the financial market. I want my site to reflect that I stand by my product and reputation means everything to me. This site has to be engaging.
• Sorry, I should have included this earlier of what I will all need on this site.
• I'll have about Tradlo (my company, what we stand for, who we work with, my strategy, etc....
• about me (why i started this company, who I am)
• Performance (graphs and recent posts of signals)
• Membership (how to sign up)
• Terms of service/legal/disclaimers
• FAQS
• Personal Development Resources
• Forex Education Resources
Nice to have
• Quick links to bounce around the site faster.
Should not have
• I do not want over the top white collar conservative.

```html
<!DOCTYPE html>
<html lang="en">
<head>
<meta charset="utf-8">
<title>Tradlo - Forex Signal Services</title>
<link rel="stylesheet" href="https://fonts.googleapis.com/css2?family=Jost:wght@400;500&family=Open+Sans:wght@400;600;700&display=swap">
<style>
:root{
  --orange:#e8832c;
  --orange-band:#e98a3c;
  --ink:#222;
  --text:#666;
  --muted:#888;
  --line:#d9d9d9;
  --light:#f4f4f4;
  --hero:#efefef;
  --white:#fff;
}
*{box-sizing:border-box;margin:0;padding:0}
html,body{width:1200px;height:3163px;overflow:hidden}
body{font-family:"Open Sans",Arial,sans-serif;color:var(--text);background:var(--white);position:relative}
.section{position:absolute;left:0;width:1200px}
.heading{font-family:"Jost",Helvetica,sans-serif;font-weight:400;color:var(--ink);letter-spacing:.3px}
.btn-outline{position:absolute;display:flex;align-items:center;justify-content:center;border:2px solid #e6b894;border-radius:24px;color:var(--orange);font-weight:700;font-size:14.5px;letter-spacing:.3px;background:var(--white)}

/* header */
.site-header{top:0;height:95px;background:var(--white);border-top:5px solid var(--orange);z-index:3;box-shadow:0 1px 3px rgba(0,0,0,.08)}
.brand{position:absolute;left:92px;top:-5px;width:160px;height:155px;border-radius:0 0 80px 80px;background:var(--white);box-shadow:0 2px 4px rgba(0,0,0,.1);display:flex;flex-direction:column;align-items:center;justify-content:center;gap:6px}
.brand-dot{width:34px;height:34px;border-radius:50%;background:var(--orange)}
.brand-name{font-family:"Jost",sans-serif;font-size:34px;color:#555;font-weight:400}
.topbar{position:absolute;top:12px;right:94px;display:flex;gap:34px;font-size:14.5px;color:#444}
.topbar span{display:flex;align-items:center;gap:12px}
.icon-ring{width:30px;height:30px;border-radius:50%;border:1.5px solid #e6b894;display:flex;align-items:center;justify-content:center;flex:none}
.main-nav{position:absolute;top:58px;left:418px;display:flex;gap:36px;font-size:15px;color:#333;align-items:center}
.main-nav .active{color:var(--orange)}

/* hero */
.hero{top:95px;height:443px;background:var(--hero)}
.hero h1{position:absolute;left:0;top:45px;width:100%;text-align:center;font-size:38px}
.hero .screen{position:absolute;left:302px;top:126px;width:596px;height:317px;border-radius:14px 14px 0 0;background:#d9d9d9;padding:22px 22px 0}
.hero .screen-inner{width:100%;height:100%;background:linear-gradient(135deg,#eef6f8,#d8ecf0)}
.hero .arrow{position:absolute;top:200px}

/* welcome */
.welcome{top:538px;height:365px;text-align:center}
.welcome h2{position:absolute;left:0;top:66px;width:100%;font-size:33px}
.welcome p{position:absolute;top:136px;left:250px;width:700px;font-size:14px;line-height:28px}

/* strategy */
.strategy{top:903px;height:434px;background:var(--light)}
.strategy .photo{position:absolute;left:0;top:0;width:601px;height:434px;background:linear-gradient(135deg,#1d3b66,#244a7e 55%,#c56a1f)}
.strategy h2{position:absolute;left:658px;top:34px;font-size:33px}
.strategy p{position:absolute;left:658px;width:420px;font-size:12.5px;line-height:24px}

/* blog */
.blog{top:1337px;height:557px}
.blog h2{position:absolute;left:0;top:56px;width:100%;text-align:center;font-size:33px}
.post{position:absolute;top:139px;width:324px}
.post .thumb{height:180px;border:1px solid var(--line);padding:6px;background:var(--white)}
.post .thumb div{height:100%}
.post h3{margin-top:24px;font-family:"Open Sans",sans-serif;font-weight:600;font-size:18.5px;color:var(--ink)}
.post .meta{margin-top:12px;font-size:12px;color:var(--muted);display:flex;align-items:center;gap:6px}
.post .meta i{color:#ccc;font-style:normal}
.post p{margin-top:12px;font-size:12.5px;line-height:20px}
.post .more{display:block;margin-top:12px;font-size:12px;font-weight:700;color:var(--orange)}

/* why us */
.why{top:1894px;height:458px;background:var(--light)}
.why .photo{position:absolute;left:601px;top:0;width:599px;height:458px;background:linear-gradient(160deg,#f1f1f1,#2f6fb5 45%,#1b4f8c 70%,#c9b79d)}
.why h2{position:absolute;left:97px;top:36px;font-size:35px;line-height:50px}
.why ul{position:absolute;left:97px;top:104px;width:460px;list-style:none}
.why li{display:flex;gap:12px;font-size:12.5px;line-height:20px;margin-bottom:14px}
.why li svg{flex:none;margin-top:3px}

/* testimonial */
.testimonial{top:2352px;height:310px;background:var(--orange-band);text-align:center;color:var(--white)}
.testimonial .quote{position:absolute;left:565px;top:40px}
.testimonial blockquote{position:absolute;left:170px;top:130px;width:860px;font-style:italic;font-size:13px;line-height:25px}
.testimonial .author{position:absolute;left:0;top:248px;width:1200px;text-align:center;font-style:normal;font-weight:700;font-size:14.5px;display:block}

/* contact */
.contact{top:2662px;height:501px}
.contact h2{position:absolute;left:0;top:60px;width:100%;text-align:center;font-size:33px}
.contact h4{position:absolute;top:138px;font-weight:600;font-size:17px;color:var(--ink)}
.field{position:absolute;border:1px solid var(--line);font-size:12px;color:var(--muted);padding:8px 14px}
.submit{position:absolute;left:626px;top:354px;width:78px;height:30px;border-radius:16px;background:var(--orange);color:var(--white);font-size:11.5px;font-weight:700;display:flex;align-items:center;justify-content:center}
.info{position:absolute;left:782px;display:flex;gap:18px;font-size:12.5px;line-height:22px;color:var(--text)}
.socials{position:absolute;left:784px;top:356px;display:flex;gap:6px}
.socials span{width:28px;height:28px;border-radius:50%}
.footer-line{position:absolute;left:97px;top:424px;width:1006px;border-top:1px solid var(--line)}
.copyright{position:absolute;left:0;top:456px;width:100%;text-align:center;font-size:12.5px;color:var(--muted)}
</style>
</head>
<body>

<header class="section site-header">
  <div class="brand"><span class="brand-dot"></span><span class="brand-name">Tradlo</span></div>
  <div class="topbar">
    <span><i class="icon-ring"><svg width="14" height="14" viewBox="0 0 24 24"><path fill="#e8832c" d="M6.6 10.8a15 15 0 006.6 6.6l2.2-2.2c.3-.3.7-.4 1-.2 1.1.4 2.3.6 3.6.6.6 0 1 .4 1 1V20c0 .6-.4 1-1 1A17 17 0 013 4c0-.6.4-1 1-1h3.5c.6 0 1 .4 1 1 0 1.3.2 2.5.6 3.6.1.3 0 .7-.2 1z"/></svg></i>1 555 010 0199</span>
    <span><i class="icon-ring"><svg width="14" height="12" viewBox="0 0 24 18"><rect x="1" y="1" width="22" height="16" rx="2" fill="none" stroke="#e8832c" stroke-width="2"/><path d="M1 2l11 8 11-8" fill="none" stroke="#e8832c" stroke-width="2"/></svg></i>info@tradlo.example</span>
  </div>
  <nav class="main-nav">
    <span class="active">Home</span><span>About Us</span><span>Features</span><span>Membership Plans</span><span>Blog</span><span>Contact Us</span>
    <svg width="17" height="17" viewBox="0 0 24 24"><circle cx="10" cy="10" r="7" fill="none" stroke="#222" stroke-width="3"/><path d="M15 15l7 7" stroke="#222" stroke-width="3"/></svg>
  </nav>
</header>

<section class="section hero">
  <h1 class="heading">Moments Matter Most. Reshape Your Path</h1>
  <svg class="arrow" style="left:36px" width="22" height="36" viewBox="0 0 22 36"><path d="M18 2L4 18l14 16" fill="none" stroke="#bbb" stroke-width="3"/></svg>
  <svg class="arrow" style="left:1142px" width="22" height="36" viewBox="0 0 22 36"><path d="M4 2l14 16L4 34" fill="none" stroke="#bbb" stroke-width="3"/></svg>
  <div class="screen"><div class="screen-inner" role="img" aria-label="Laptop screen showing rising green, blue and magenta forex trend lines on a grid"></div></div>
</section>

<section class="section welcome">
  <h2 class="heading">Welcome to Tradlo</h2>
  <p>We use proven strategies to help traders in succeeding in the forex market. Our forex experts provide high-probability, professional and consistent forex signals and charts that help traders in maximizing their profits and eliminating losses.</p>
  <a class="btn-outline" style="left:437px;top:246px;width:326px;height:42px">TRY OUR FREE CURRENCY EDUCATION</a>
</section>

<section class="section strategy">
  <div class="photo" role="img" aria-label="Close-up of an orange forex price chart on a dark blue trading screen"></div>
  <h2 class="heading">Our Strategy</h2>
  <p style="top:100px">tradlo.example works with both day as well as intraday traders. We only hold a maximum of one position at any given point in time. Once we’ve placed an order we do not move SL or TP targets.</p>
  <p style="top:196px">We follow naked forex trading techniques including price action, immediate trend and personalized mathematical formulas. Our success stems from our strict enforcement of discipline, patience, attitude, economics and timing to help our traders maximize their gains from forex trading. (please edit) At Tradlo, we trade GBP/USD, EUR/USD, AUD/USD, USD/CHF.</p>
  <a class="btn-outline" style="left:658px;top:354px;width:415px;height:40px">CLICK HERE TO LEARN MORE ABOUT FOREX BASICS!</a>
</section>

<section class="section blog">
  <h2 class="heading">Latest Blog</h2>
  <article class="post" style="left:97px">
    <div class="thumb"><div role="img" aria-label="Tablet displaying business bar and pie charts" style="background:linear-gradient(135deg,#dfe7ef,#9fb6cc)"></div></div>
    <h3>Finibus Bonorum et Malorum</h3>
    <div class="meta"><svg width="11" height="11" viewBox="0 0 12 12"><rect x="1" y="2" width="10" height="9" fill="#e8832c"/></svg>20/01/2016 <i>|</i> <svg width="11" height="11" viewBox="0 0 12 12"><circle cx="6" cy="4" r="3" fill="#e8832c"/><path d="M1 12a5 5 0 0110 0z" fill="#e8832c"/></svg>Mark <i>|</i> <svg width="12" height="11" viewBox="0 0 12 11"><path d="M1 1h10v7H5l-3 3V8H1z" fill="none" stroke="#e8832c" stroke-width="1.4"/></svg>3 Comments</div>
    <p>Nam libero tempore, cum soluta nobis est eligendi optio cumque nihil impedit quo minus id quod maxim.</p>
    <a class="more">READ MORE &gt;&gt;</a>
  </article>
  <article class="post" style="left:443px">
    <div class="thumb"><div role="img" aria-label="Dark trading screen with multicoloured market lines" style="background:linear-gradient(135deg,#1a1a1a,#2d3b2a 60%,#5a2020)"></div></div>
    <h3>Finibus Bonorum et Malorum</h3>
    <div class="meta"><svg width="11" height="11" viewBox="0 0 12 12"><rect x="1" y="2" width="10" height="9" fill="#e8832c"/></svg>20/01/2016 <i>|</i> <svg width="11" height="11" viewBox="0 0 12 12"><circle cx="6" cy="4" r="3" fill="#e8832c"/><path d="M1 12a5 5 0 0110 0z" fill="#e8832c"/></svg>Mark <i>|</i> <svg width="12" height="11" viewBox="0 0 12 11"><path d="M1 1h10v7H5l-3 3V8H1z" fill="none" stroke="#e8832c" stroke-width="1.4"/></svg>3 Comments</div>
    <p>Nam libero tempore, cum soluta nobis est eligendi optio cumque nihil impedit quo minus id quod maxim.</p>
    <a class="more">READ MORE &gt;&gt;</a>
  </article>
  <article class="post" style="left:785px">
    <div class="thumb"><div role="img" aria-label="Printed blue bar charts on a desk during a meeting" style="background:linear-gradient(135deg,#cfd8e2,#f2f4f6 50%,#5c87bf)"></div></div>
    <h3>Finibus Bonorum et Malorum</h3>
    <div class="meta"><svg width="11" height="11" viewBox="0 0 12 12"><rect x="1" y="2" width="10" height="9" fill="#e8832c"/></svg>20/01/2016 <i>|</i> <svg width="11" height="11" viewBox="0 0 12 12"><circle cx="6" cy="4" r="3" fill="#e8832c"/><path d="M1 12a5 5 0 0110 0z" fill="#e8832c"/></svg>Mark <i>|</i> <svg width="12" height="11" viewBox="0 0 12 11"><path d="M1 1h10v7H5l-3 3V8H1z" fill="none" stroke="#e8832c" stroke-width="1.4"/></svg>3 Comments</div>
    <p>Nam libero tempore, cum soluta nobis est eligendi optio cumque nihil impedit quo minus id quod maxim.</p>
    <a class="more">READ MORE &gt;&gt;</a>
  </article>
</section>

<section class="section why">
  <h2 class="heading">Why Us?</h2>
  <ul>
    <li><svg width="13" height="13" viewBox="0 0 14 14"><circle cx="7" cy="7" r="7" fill="#e8832c"/><path d="M4 7l2 2 4-4" fill="none" stroke="#fff" stroke-width="1.8"/></svg>We offer speedy, consistent, accurate and desired results.</li>
    <li><svg width="13" height="13" viewBox="0 0 14 14"><circle cx="7" cy="7" r="7" fill="#e8832c"/><path d="M4 7l2 2 4-4" fill="none" stroke="#fff" stroke-width="1.8"/></svg>We’re a highly dependable and trusted forex trading platform.</li>
    <li><svg width="13" height="13" viewBox="0 0 14 14"><circle cx="7" cy="7" r="7" fill="#e8832c"/><path d="M4 7l2 2 4-4" fill="none" stroke="#fff" stroke-width="1.8"/></svg>Our motto is to ‘Reshape Your Path’ and also to ensure that you earn profits on a regular basis.</li>
    <li><svg width="13" height="13" viewBox="0 0 14 14"><circle cx="7" cy="7" r="7" fill="#e8832c"/><path d="M4 7l2 2 4-4" fill="none" stroke="#fff" stroke-width="1.8"/></svg>Our objective is to provide global access to trusted forex signals.</li>
    <li><svg width="13" height="13" viewBox="0 0 14 14"><circle cx="7" cy="7" r="7" fill="#e8832c"/><path d="M4 7l2 2 4-4" fill="none" stroke="#fff" stroke-width="1.8"/></svg>Our services are highly affordable.</li>
    <li><svg width="13" height="13" viewBox="0 0 14 14"><circle cx="7" cy="7" r="7" fill="#e8832c"/><path d="M4 7l2 2 4-4" fill="none" stroke="#fff" stroke-width="1.8"/></svg>We offer High Probable forex strategies with high rewards.</li>
    <li><svg width="13" height="13" viewBox="0 0 14 14"><circle cx="7" cy="7" r="7" fill="#e8832c"/><path d="M4 7l2 2 4-4" fill="none" stroke="#fff" stroke-width="1.8"/></svg>We set transparent entry price and exit levels.</li>
    <li><svg width="13" height="13" viewBox="0 0 14 14"><circle cx="7" cy="7" r="7" fill="#e8832c"/><path d="M4 7l2 2 4-4" fill="none" stroke="#fff" stroke-width="1.8"/></svg>Our team will constantly update you regarding the status of your trade till the time it is closed.</li>
  </ul>
  <div class="photo" role="img" aria-label="Hands holding a tablet that shows a blue stock market chart"></div>
</section>

<section class="section testimonial">
  <svg class="quote" width="70" height="60" viewBox="0 0 70 60"><path d="M4 58V34C4 16 12 5 28 2v9c-8 3-12 9-12 19h12v28zm38 0V34c0-18 8-29 24-32v9c-8 3-12 9-12 19h12v28z" fill="#fff"/></svg>
  <blockquote>At vero eos et accusamus et iusto odio dignissimos ducimus qui blanditiis praesentium voluptatum deleniti atque corrupti quos dolores et quas molestias excepturi sint occaecati cupiditate non provident, similique sunt in culpa qui officia deserunt mollitia animi, id est laborum et dolorum fuga. Et harum quidem rerum facilis est et expedita distinctio.</blockquote>
  <p class="author">ALEX REED</p>
</section>

<section class="section contact">
  <h2 class="heading">Contact Us</h2>
  <h4 style="left:97px">Get In Touch:</h4>
  <div class="field" style="left:99px;top:183px;width:297px;height:32px">Name :</div>
  <div class="field" style="left:407px;top:183px;width:297px;height:32px">Phone :</div>
  <div class="field" style="left:99px;top:227px;width:605px;height:32px">Email :</div>
  <div class="field" style="left:99px;top:272px;width:605px;height:67px">Message :</div>
  <div class="submit">SUBMIT</div>

  <h4 style="left:782px">Contact Information</h4>
  <div class="info" style="top:184px"><i class="icon-ring"><svg width="12" height="15" viewBox="0 0 12 16"><path d="M6 0a6 6 0 00-6 6c0 4.5 6 10 6 10s6-5.5 6-10a6 6 0 00-6-6z" fill="#e8832c"/><circle cx="6" cy="6" r="2" fill="#fff"/></svg></i><span>410 Harbor Lane, 12th Floor<br>Springfield, ST 00000</span></div>
  <div class="info" style="top:243px"><i class="icon-ring"><svg width="13" height="13" viewBox="0 0 24 24"><path fill="#e8832c" d="M6.6 10.8a15 15 0 006.6 6.6l2.2-2.2c.3-.3.7-.4 1-.2 1.1.4 2.3.6 3.6.6.6 0 1 .4 1 1V20c0 .6-.4 1-1 1A17 17 0 013 4c0-.6.4-1 1-1h3.5c.6 0 1 .4 1 1 0 1.3.2 2.5.6 3.6.1.3 0 .7-.2 1z"/></svg></i><span style="line-height:30px">1 555 010 0199</span></div>
  <div class="info" style="top:296px"><i class="icon-ring"><svg width="13" height="10" viewBox="0 0 24 18"><rect x="1" y="1" width="22" height="16" rx="2" fill="none" stroke="#e8832c" stroke-width="2"/><path d="M1 2l11 8 11-8" fill="none" stroke="#e8832c" stroke-width="2"/></svg></i><span style="line-height:30px">info@tradlo.example</span></div>
  <div class="socials"><span style="background:#2c4a86"></span><span style="background:#2ea3dc"></span><span style="background:#d52b2b"></span><span style="background:#8b7356"></span></div>

  <div class="footer-line"></div>
  <p class="copyright">Copyrights © 2017, Tradlo. All Rights Reserved.</p>
</section>

</body>
</html>
```